Social Media Graphics - Oakline Push REVISED

Create 6-7 individual social media graphics (square size) to encourage folks to join our online course called:

The Harvest Ledger Circle
How to Launch a Multi-Million Business From Scratch
Sign Up Today!

IMPORTANT: Make the largest and most prominent text on the graphic be: How to Launch a Multi-Million Business From Scratch

For the color scheme of the graphics, let's try a blue color palette; make sure the graphics appeal to both men and women

Make sure each graphic contains 1 of the 3 pics attached (crop pic as needed); and make sure one of the graphics is all TEXT only.

Target Market(s)

men and women looking to start a business

Industry/Entity Type

Entrepreneurship

Colors
0054AA
0677BA
7BADD7
CADEEF
E8F1F8

Requirements
Must have
• All the text and use the 3 pics provided; one graphic can be all text; Simple, modern design that's easy to read

```html
<!DOCTYPE html>
<html lang="en">
<head>
<meta charset="utf-8">
<title>The Harvest Ledger Circle – Social Graphics</title>
<link href="https://fonts.googleapis.com/css2?family=Bebas+Neue&family=Oswald:wght@500;600&family=Poppins:wght@600;700;800&display=swap" rel="stylesheet">
<style>
  :root {
    --board: #919191;
    --blue: #0054aa;
    --blue-mid: #0677ba;
    --blue-bright: #1e98e0;
    --blue-soft: #7badd7;
    --blue-pale: #cadeef;
    --blue-mist: #e8f1f8;
    --navy: #062b5e;
    --navy-deep: #04204a;
    --white: #ffffff;
    --photo-warm: #6b5d5a;
  }
  * { margin: 0; padding: 0; box-sizing: border-box; }
  html, body { width: 881px; height: 1200px; overflow: hidden; }
  body { background: var(--board); position: relative; font-family: "Bebas Neue", sans-serif; color: var(--white); }

  .tile { position: absolute; width: 291px; height: 291px; overflow: hidden; background: var(--blue); }
  .tile--one   { left: 140px; top: 132px; background: linear-gradient(180deg, #0b62c3 0%, var(--blue-bright) 50%, #0b5fbf 100%); }
  .tile--two   { left: 454px; top: 132px; background: radial-gradient(circle at 50% 55%, #1a7ad6 0%, var(--blue) 70%); }
  .tile--three { left: 140px; top: 454px; }
  .tile--four  { left: 454px; top: 454px; }
  .tile--five  { left: 139px; top: 776px; }
  .tile--six   { left: 455px; top: 774px; background: linear-gradient(180deg, var(--blue-mid) 20%, var(--blue) 100%); }

  .abs { position: absolute; }
  .headline { font-family: "Bebas Neue", sans-serif; line-height: 1; white-space: nowrap; }
  .center { left: 0; right: 0; text-align: center; }
  .photo { position: absolute; }

  /* CTA stacked buttons */
  .cta-back { position: absolute; background: var(--navy); border: 1.5px solid var(--white); }
  .cta-back::before { content: ""; position: absolute; inset: 4px -1px -1px 4px; background: var(--navy-deep); }
  .cta-tag { position: absolute; font-family: "Poppins", sans-serif; font-weight: 700; text-align: center; letter-spacing: .5px; }
  .cta-word { position: absolute; font-family: "Poppins", sans-serif; font-weight: 800; text-align: center; color: var(--white); z-index: 1; }

  .spaced { font-family: "Oswald", sans-serif; font-weight: 500; letter-spacing: 2.5px; white-space: nowrap; }

  .badge { position: absolute; border-radius: 50%; background: var(--navy); border: 3px solid var(--blue-bright); box-shadow: 0 0 0 3px var(--blue); display: flex; align-items: center; justify-content: center; text-align: center; font-family: "Bebas Neue", sans-serif; line-height: 1.05; }
  .badge::after { content: ""; position: absolute; inset: 4px; border-radius: 50%; border: 1px dotted var(--blue-pale); }
</style>
</head>
<body>

<!-- Tile 1 -->
<section class="tile tile--one">
  <p class="abs center headline" style="top:11px;font-size:25px;">The Harvest Ledger Circle</p>
  <div class="photo" role="img" aria-label="Photo of the two course hosts smiling, man in black turtleneck and woman in denim jacket" style="left:52px;top:42px;width:171px;height:90px;background:linear-gradient(180deg,rgba(30,152,224,0) 0%,var(--photo-warm) 45%,#1c2433 100%);border-radius:40px 40px 0 0;opacity:.85;"></div>
  <p class="abs center headline" style="top:125px;font-size:33px;">How to launch a</p>
  <p class="abs center headline" style="top:157px;font-size:33px;">Multi-million business</p>
  <p class="abs center headline" style="top:190px;font-size:33px;">From scratch</p>
  <span class="abs" style="left:22px;top:206px;width:37px;height:2px;background:var(--white);"></span>
  <span class="abs" style="left:232px;top:206px;width:37px;height:2px;background:var(--white);"></span>
  <div class="cta-back" style="left:74px;top:241px;width:143px;height:39px;"></div>
  <div class="cta-tag" style="left:96px;top:227px;width:99px;height:21px;background:var(--white);color:var(--navy);font-size:13px;line-height:21px;z-index:2;">SIGN UP</div>
  <div class="cta-word" style="left:74px;top:252px;width:143px;font-size:18px;line-height:22px;letter-spacing:1px;">TODAY!</div>
</section>

<!-- Tile 2 -->
<section class="tile tile--two">
  <div class="abs spaced" style="left:14px;top:16px;width:267px;height:29px;background:var(--navy);border-radius:15px;border-top:1.5px solid var(--white);text-align:center;font-size:15px;line-height:28px;letter-spacing:2px;">THE HARVEST LEDGER CIRCLE</div>
  <p class="abs headline" style="left:11px;top:54px;font-size:27px;">How to launch a multi-million</p>
  <p class="abs headline" style="left:11px;top:86px;font-size:27px;">Business from scratch</p>
  <div class="photo" role="img" aria-label="Photo of the two course hosts smiling, woman in coral top and man in black jacket" style="left:42px;top:119px;width:198px;height:172px;background:linear-gradient(180deg,#3b2f2e 0%,#7a5552 45%,#c8485a 80%,#1b1b22 100%);border-radius:60px 60px 0 0;opacity:.9;"></div>
  <div class="cta-back" style="left:60px;top:224px;width:171px;height:53px;"></div>
  <div class="cta-tag" style="left:87px;top:213px;width:119px;height:25px;background:var(--blue-mid);color:var(--white);font-size:15px;line-height:25px;z-index:2;">SIGN UP</div>
  <div class="cta-word" style="left:60px;top:242px;width:171px;font-size:23px;line-height:28px;letter-spacing:1px;">TODAY!</div>
</section>

<!-- Tile 3 -->
<section class="tile tile--three">
  <div class="abs spaced" style="left:0;top:18px;width:291px;height:28px;background:var(--navy);text-align:center;font-size:17px;line-height:28px;letter-spacing:2.5px;">THE HARVEST LEDGER CIRCLE</div>
  <div class="photo" role="img" aria-label="Photo of the two course hosts smiling over a light blue paint splash" style="left:18px;top:47px;width:260px;height:118px;background:linear-gradient(90deg,var(--blue-soft) 0%,#5c4a48 25%,#d04a63 45%,#2a2526 70%,var(--blue-soft) 100%);opacity:.85;"></div>
  <div class="badge" style="left:190px;top:81px;width:86px;height:86px;font-size:19px;">SIGN UP<br>TODAY!</div>
  <div class="abs" style="left:5px;top:163px;width:282px;height:121px;border:1px solid var(--blue-pale);background:var(--blue);"></div>
  <p class="abs center headline" style="top:172px;font-size:33px;">How to launch a</p>
  <p class="abs center headline" style="top:207px;font-size:33px;">Multi-million business</p>
  <p class="abs center headline" style="top:242px;font-size:33px;">From scratch</p>
</section>

<!-- Tile 4 -->
<section class="tile tile--four">
  <div class="abs" style="left:0;top:0;width:291px;height:32px;background:var(--white);"></div>
  <p class="abs center headline" style="top:4px;font-size:27px;color:var(--blue);">The Harvest Ledger Circle</p>
  <p class="abs headline" style="left:17px;top:46px;font-size:44px;">How to launch a</p>
  <p class="abs headline" style="left:17px;top:91px;font-size:26px;">Multi-million</p>
  <p class="abs headline" style="left:17px;top:123px;font-size:26px;">Business</p>
  <p class="abs headline" style="left:17px;top:155px;font-size:26px;">From</p>
  <p class="abs headline" style="left:17px;top:187px;font-size:26px;">Scratch</p>
  <div class="photo" role="img" aria-label="Photo of the two hosts on stage, man speaking into a microphone and woman laughing" style="left:103px;top:114px;width:200px;height:190px;border-radius:100px 0 0 0;background:linear-gradient(180deg,var(--blue-mist) 0%,#b9a99a 50%,#2a2a2e 100%);border-top:4px solid var(--white);border-left:4px solid var(--white);"></div>
  <div class="badge" style="left:16px;top:219px;width:66px;height:66px;font-size:14px;background:var(--blue);">SIGN UP<br>TODAY!</div>
</section>

<!-- Tile 5 -->
<section class="tile tile--five">
  <p class="abs headline" style="left:16px;top:12px;font-size:29px;">The Harvest Ledger Circle</p>
  <span class="abs" style="left:0;top:50px;width:291px;height:1px;background:var(--blue-pale);"></span>
  <p class="abs headline" style="left:19px;top:62px;font-size:44px;">How to launch a</p>
  <p class="abs headline" style="left:19px;top:106px;font-size:44px;">Multi-million</p>
  <p class="abs headline" style="left:19px;top:150px;font-size:44px;">Business</p>
  <p class="abs headline" style="left:19px;top:199px;font-size:28px;">From scratch</p>
  <div class="photo" role="img" aria-label="Photo of the two course hosts, man with arms crossed in black turtleneck and woman in denim jacket" style="left:157px;top:139px;width:134px;height:152px;background:linear-gradient(180deg,#6d5148 0%,#2a2124 40%,#151519 100%);border-radius:50px 0 0 0;opacity:.9;"></div>
  <div class="abs" style="left:18px;top:242px;width:136px;height:29px;border-radius:15px;background:var(--navy);border:1.5px solid var(--white);border-left-width:4px;border-left-color:var(--navy-deep);font-family:'Poppins',sans-serif;font-weight:700;font-size:11px;line-height:26px;text-align:center;">SIGN UP TODAY!</div>
</section>

<!-- Tile 6 -->
<section class="tile tile--six">
  <div class="abs" style="left:0;top:0;width:291px;height:45px;background:var(--navy);opacity:.55;"></div>
  <div class="abs" style="left:10px;top:23px;width:272px;height:163px;border:1px solid var(--blue-pale);border-top:none;"></div>
  <span class="abs" style="left:10px;top:23px;width:14px;height:1px;background:var(--blue-pale);"></span>
  <span class="abs" style="left:268px;top:23px;width:14px;height:1px;background:var(--blue-pale);"></span>
  <p class="abs center headline" style="top:9px;font-size:27px;">The Harvest Ledger Circle</p>
  <p class="abs center headline" style="top:59px;font-size:33px;">How to launch a</p>
  <p class="abs center headline" style="top:100px;font-size:33px;">Multi-million business</p>
  <p class="abs center headline" style="top:141px;font-size:33px;">From scratch</p>
  <div class="cta-back" style="left:61px;top:212px;width:171px;height:52px;"></div>
  <div class="cta-tag" style="left:87px;top:201px;width:119px;height:25px;background:var(--blue-mid);color:var(--white);font-size:15px;line-height:25px;z-index:2;">SIGN UP</div>
  <div class="cta-word" style="left:61px;top:229px;width:171px;font-size:23px;line-height:28px;letter-spacing:1px;">TODAY!</div>
</section>

</body>
</html>
```